Computer consultant business card

Bexil Software is a newly started computer consulting company. It's a small one-man company that provides mostly Vornix applications but also websites in collaboration with designers. I'm running this company on the side of full time university studies.

I want the final design to be clean and memorable. Be creative! :)

Some inspiration:
http://www.pixelmarta.com/design/48317
http://www.pixelmarta.com/design/2739164/business-card-design-by-frostlynk
http://www.pixelmarta.com/design/604281/business-card-design-by-koralind-vestrabanu

See attachment for my company logo.
Updates

I would like to thank everyone for submitting! I'll need a couple of days to review and ultimately select a design.

Target Market(s)

Non-technical entrepreneurs and small companies.

Industry/Entity Type

University

Requirements
Must have
• My company logo.
In any way, both colors from my logo.
First- and last name, e-mail and phone number.
Double-sided design.
Nice to have
• Something creative with the symbol in my logo

```html
<!DOCTYPE html>
<html lang="en">
<head>
<meta charset="utf-8">
<title>Bexil Software – Business Card</title>
<link rel="stylesheet" href="https://fonts.googleapis.com/css2?family=Jost:wght@400;500;600&display=swap">
<style>
  :root {
    --brand-blue: #2179fb;
    --brand-dark: #333333;
    --card-white: #ffffff;
    --stage: #ece8e3;
  }
  * { margin: 0; padding: 0; box-sizing: border-box; }
  html, body {
    width: 1200px; height: 782px; overflow: hidden;
    background: var(--stage);
    font-family: "Jost", sans-serif;
  }
  .canvas { position: relative; width: 1200px; height: 782px; }

  .card {
    position: absolute;
    width: 600px; height: 300px;
    border-radius: 24px 150px 150px 24px;
    overflow: hidden;
  }

  /* Front side */
  .card-front {
    left: 40px; top: 60px;
    background: var(--brand-blue);
    border: 12px solid var(--card-white);
    color: var(--card-white);
    box-shadow: 0 2px 6px rgba(0,0,0,.15);
  }
  .front-mark {
    position: absolute; left: 52px; top: 62px;
    width: 152px; height: 152px; border-radius: 50%;
    background: var(--card-white);
  }
  .front-divider {
    position: absolute; left: 250px; top: 0; bottom: 0;
    width: 2px; background: rgba(255,255,255,.35);
  }
  .front-info { position: absolute; left: 282px; top: 18px; }
  .brand-name {
    font-weight: 500; font-size: 54px; line-height: 1; letter-spacing: 1px;
  }
  .person { margin-top: 18px; }
  .first-name { font-weight: 600; font-size: 22px; line-height: 1.1; }
  .last-name { font-weight: 400; font-size: 18px; line-height: 1.1; }
  .contact { margin-top: 18px; list-style: none; font-size: 15px; }
  .contact li { display: flex; align-items: center; gap: 8px; line-height: 1.55; }
  .contact svg { width: 12px; height: 12px; fill: var(--card-white); }
  .address { margin-top: 14px; font-size: 15px; line-height: 1.35; }

  /* Back side */
  .card-back {
    left: 560px; top: 420px;
    background: var(--card-white);
    border: 12px solid var(--brand-dark);
    display: flex; align-items: center; gap: 34px;
    padding-left: 60px;
  }
  .back-mark {
    width: 120px; height: 120px; border-radius: 50%;
    background: var(--brand-blue);
    flex: none;
  }
  .back-name {
    font-weight: 500; font-size: 110px; line-height: 1;
    color: var(--brand-dark); letter-spacing: 2px;
  }
</style>
</head>
<body>
<main class="canvas">
  <section class="card card-front" aria-label="Card front">
    <div class="front-mark"></div>
    <div class="front-divider"></div>
    <div class="front-info">
      <div class="brand-name">bexil</div>
      <div class="person">
        <div class="first-name">First Name</div>
        <div class="last-name">Last Name</div>
      </div>
      <ul class="contact">
        <li>
          <svg viewBox="0 0 24 24" aria-hidden="true"><path d="M6.6 10.8a15 15 0 0 0 6.6 6.6l2.2-2.2a1 1 0 0 1 1-.25 11.4 11.4 0 0 0 3.6.57 1 1 0 0 1 1 1V20a1 1 0 0 1-1 1A17 17 0 0 1 3 4a1 1 0 0 1 1-1h3.5a1 1 0 0 1 1 1c0 1.25.2 2.45.57 3.57a1 1 0 0 1-.25 1z"/></svg>
          0412 738596
        </li>
        <li>
          <svg viewBox="0 0 24 24" aria-hidden="true"><path d="M2 5h20v14H2z M3 6l9 7 9-7" fill="none" stroke="#fff" stroke-width="2.4"/></svg>
          info@bexil.com
        </li>
      </ul>
      <div class="address">12, Harbor Court<br>Lenton, State 0318</div>
    </div>
  </section>

  <section class="card card-back" aria-label="Card back">
    <div class="back-mark"></div>
    <div class="back-name">bexil</div>
  </section>
</main>
</body>
</html>
```